Bry7Legal Letterhead

Need a new letterhead for my law firm.
IDENTIFYING INFORMATION BELOW:
Anselmo R Quintara III
Attorney at Law
Address: 2847 Larkspur Blvd, Ste 300, Dallas, TX 75204
Phone: 877-482-6017
Fax: 469-738-1452
Email: bry@bry7legal.example
Website: www.bry7legal.example

Colors
0054AA
0677BA
7BADD7
CADEEF
E8F1F8

Requirements
Must have
• Logo needs to be on the letterhead, along with identifying information which is included in the project description.

```html
<!DOCTYPE html>
<html lang="en">
<head>
<meta charset="utf-8">
<title>Bry7Legal Letterhead</title>
<link href="https://fonts.googleapis.com/css2?family=Montserrat:wght@300;400;500&family=Arimo:wght@400&display=swap" rel="stylesheet">
<style>
  :root {
    --navy: #0054AA;
    --blue: #0677BA;
    --mist: #7BADD7;
    --ice: #CADEEF;
    --frost: #E8F1F8;
    --ink: #1a1a1a;
    --text: #8a8a8a;
    --text-dark: #333333;
    --backdrop: #ececec;
  }
  * { margin: 0; padding: 0; box-sizing: border-box; }
  html, body { width: 1200px; height: 1200px; overflow: hidden; }
  body { background: var(--backdrop); font-family: "Montserrat", sans-serif; position: relative; }
  .sheet {
    position: absolute; left: 190px; top: 20px; width: 821px; height: 1160px;
    background: #fff; box-shadow: 0 2px 10px rgba(0,0,0,.12);
  }
  .header-band { position: absolute; left: 0; top: 0; width: 821px; height: 14px; background: var(--navy); }
  .header-rule { position: absolute; left: 0; top: 20px; width: 821px; height: 3px; background: var(--ice); }
  .brand { position: absolute; right: 42px; top: 62px; text-align: right; }
  .brand-name { display: flex; align-items: center; justify-content: flex-end; gap: 10px;
    font-weight: 500; font-size: 34px; color: var(--ink); line-height: 1; }
  .brand-mark { width: 14px; height: 14px; background: var(--blue); }
  .brand-tagline { font-weight: 500; font-size: 14px; letter-spacing: 1px; color: var(--text-dark); margin-top: 10px; }
  .recipient { position: absolute; left: 84px; top: 262px; }
  .recipient-label { font-size: 15px; letter-spacing: 2px; color: var(--text-dark); font-weight: 400; }
  .recipient-name { font-size: 14px; color: var(--blue); margin-top: 8px; }
  .recipient-address { font-size: 11.5px; color: var(--text); line-height: 18px; margin-top: 4px; }
  .letter-date { position: absolute; right: 84px; top: 263px; font-size: 12px; color: var(--text-dark); }
  .letter-body { position: absolute; left: 84px; top: 418px; width: 656px; font-size: 11.7px; font-weight: 300;
    letter-spacing: -0.1px; line-height: 14.6px; color: var(--text); text-align: justify; }
  .letter-body p { margin-bottom: 14.6px; }
  .signature-mark { position: absolute; left: 84px; top: 818px; width: 140px; height: 32px; border-radius: 4px;
    background: linear-gradient(90deg, var(--frost), #fff); }
  .signer { position: absolute; left: 82px; top: 861px; }
  .signer-name { font-size: 13.5px; color: var(--text-dark); }
  .signer-title { font-size: 11px; color: var(--text); margin-top: 3px; }
  .sheet-footer { position: absolute; left: 0; right: 0; top: 1086px; font-family: "Arimo", sans-serif; font-size: 13.5px; color: var(--text-dark); text-align: center; }
  .footer-address { display: flex; align-items: center; justify-content: center; gap: 6px; }
  .footer-address::before, .footer-address::after { content: ""; width: 88px; height: 1px; background: var(--text-dark); }
  .footer-contacts { display: flex; justify-content: center; gap: 10px; margin-top: 8px; }
  .contact-item { display: inline-flex; align-items: center; gap: 5px; }
  .contact-item svg { width: 12px; height: 12px; fill: var(--blue); }
</style>
</head>
<body>
  <div class="sheet">
    <div class="header-band"></div>
    <div class="header-rule"></div>

    <div class="brand">
      <div class="brand-name"><span class="brand-mark"></span>Bry7Legal</div>
      <div class="brand-tagline">Attorney at Law</div>
    </div>

    <div class="recipient">
      <div class="recipient-label">TO</div>
      <div class="recipient-name">Delia Harcourt</div>
      <div class="recipient-address">Human Resources<br>Northvale Systems Inc.<br>4410 Crestline Rd, Unit B<br>TX 75230 USA</div>
    </div>
    <div class="letter-date">Friday, 01/01/2018</div>

    <div class="letter-body">
      <p>Lorem ipsum dolor sit amet, consectetuer adipiscing elit, sed diam nonmmy nibh euismod tincidunt ut laoreet dolore magna aliquam erat volutpat. Ut wisi enim ad minim veniam, quis nostrud exerci tationmcorper suscipit lobortis nisl ut aliquip ex ea commodo consequat. Duis autem vel eum iriure dolor in hendrerit in vulputate velit esse molestie consequat, vel illum dolore eu feugiat nulla facilisis at vero eros et accumsan et iusto odio dignissim qui blandit praesent luptatum zzril delenit augue duis dolore te feugait nulla facilisi.</p>
      <p>Nam liber tempor cum soluta nobis eleifend option congue nihil imprdiet doming id quod mazim placerat facer possim assum. Typi non habent claritatem insitam;</p>
      <p>Est usus legentis in iis qui facit eorum claritatem.</p>
      <p>Investigationes demonstraverunt lectores legere me lius quod ii legunt saepius. Claritas est etiam processus dynamicus, qui sequitur mutationem consuetudium lectorum. Mirum est notare quam littera gothica, quam nunc putamus parum claram, anteposuerit litterarum formas humanitatis per seacula quarta decima et quinta decima. Eodem modo typi, qui nunc nobis videntur parum clari, fiant sollemnes in futurum.</p>
      <p>consectetuer adipiscing elit, sed diam nonummy nibh euismod tincidunt ut laoreet dolore magna aliquam erat volutpat. Ut wisi enim ad minim veniam, quis nostrud exerci tation ullamcorper suscipit lobortis nisl ut aliquip ex ea commodo consequat. Duis autem vel eum iriure dolor in hendrerit in vulputate velit esse molestie consequat, vel illum dolore eu feugiat nulla facilisis at vero eros et accumsan et iusto odio dignissim qui blandit praesent luptatum zzril delenit augue duis dolore te feugait nulla facilisi.</p>
      <p>Nam liber tempor cum soluta nobis eleifend option congue nihil imperdiet .</p>
    </div>

    <div class="signature-mark" role="img" aria-label="Handwritten signature of the managing director"></div>
    <div class="signer">
      <div class="signer-name">Anselmo R Quintara III</div>
      <div class="signer-title">Managing Director</div>
    </div>

    <div class="sheet-footer">
      <div class="footer-address">2847 Larkspur Blvd, Ste 300, Dallas, TX 75204</div>
      <div class="footer-contacts">
        <span class="contact-item"><svg viewBox="0 0 24 24"><path d="M6.6 10.8a15.1 15.1 0 0 0 6.6 6.6l2.2-2.2a1 1 0 0 1 1-.25 11.4 11.4 0 0 0 3.6.57 1 1 0 0 1 1 1V20a1 1 0 0 1-1 1A17 17 0 0 1 3 4a1 1 0 0 1 1-1h3.5a1 1 0 0 1 1 1c0 1.25.2 2.45.57 3.57a1 1 0 0 1-.25 1z"/></svg>877-482-6017</span>
        <span class="contact-item"><svg viewBox="0 0 24 24"><path d="M6 2h10v6H6zM3 9h18v9h-3v4H6v-4H3zm5 6v5h8v-5z"/></svg>469-738-1452</span>
        <span class="contact-item"><svg viewBox="0 0 24 24"><path d="M2 5h20v14H2zm2 2v.5l8 5 8-5V7z"/></svg>bry@bry7legal.example</span>
        <span class="contact-item"><svg viewBox="0 0 24 24"><circle cx="12" cy="12" r="10"/></svg>www.bry7legal.example</span>
      </div>
    </div>
  </div>
</body>
</html>
```